Brookvale Building Company - advertisement poster

I am looking to print some canvas signs to advertise my general contracting company, Brookvale Building Company. The sign will measure 6' long x 3' high so the size should match that ratio. I already have a logo icon, which is the Letter 'B' and some trees that I would like to incorporate, see attached. I would also like the to have the following information listed:
1) phone number: 831-555-0172
2) email: brookvalebuildingcompany@mailnest.example
3) website: brookvalebuildingcompany.example
4) Lic#4826130
5) I want to use this text: "BUILD WITH THE B-CREW!"

The ad should be relatively simple and clean. Black and Green are my company colors. I am open to creative ideas!

Target Market(s)

People looking to renovate their homes

Industry/Entity Type

Construction

Colors
59FF00
82FF00
B8FF75
E3FFCB
F4FFEA

Requirements
Must have
• Must have my company logo
Should not have
• No photos or complex graphics

```html
<!DOCTYPE html>
<html lang="en">
<head>
<meta charset="utf-8">
<title>Brookvale Building Company – Sign</title>
<link href="https://fonts.googleapis.com/css2?family=Montserrat:ital,wght@0,300;0,600;0,700;0,800;1,300;1,700;1,800&family=Anton&display=swap" rel="stylesheet">
<style>
  :root{
    --black:#000;
    --ink:#151515;
    --band-dark:#262626;
    --band-light:#4a4a4a;
    --green:#7dc242;
    --green-mid:#5a9a33;
    --green-deep:#3a7d22;
    --green-shadow:#2f5a1c;
    --silver-dark:#9a9a9a;
    --silver-light:#e6e6e6;
    --white:#fff;
    --page:#fff;
  }
  *{margin:0;padding:0;box-sizing:border-box}
  html,body{width:1200px;height:706px;overflow:hidden;background:var(--page)}
  .canvas{position:relative;width:1200px;height:706px;background:var(--page)}
  .sign{position:absolute;left:90px;top:94px;width:1020px;height:518px;overflow:hidden;
        background:linear-gradient(90deg,var(--silver-dark) 0%,var(--silver-light) 30%,#c4c4c4 60%,var(--silver-dark) 100%);
        box-shadow:0 2px 10px rgba(0,0,0,.18)}
  .top-panel{position:absolute;left:0;top:0;width:100%;height:267px;background:var(--black)}
  .sweep{position:absolute;left:0;top:0;width:1020px;height:518px}

  .brand{position:absolute;left:48px;top:40px;width:296px;text-align:center;color:var(--white);
         font-family:"Montserrat",sans-serif;font-weight:700;line-height:1}
  .brand-mark{display:block;width:44px;height:44px;margin:0 auto 18px;background:var(--green)}
  .brand-name{font-size:37px;letter-spacing:1px}
  .brand-sub{font-size:17px;letter-spacing:5px;margin-top:8px}

  .lic-rule{position:absolute;left:0;top:227px;width:474px;height:2px;background:var(--green)}
  .lic{position:absolute;left:86px;top:206px;width:221px;height:43px;border-radius:14px 22px 22px 14px;
       transform:skewX(-12deg);background:linear-gradient(90deg,#bdbdbd,#f0f0f0 50%,#bdbdbd)}
  .lic span{position:absolute;inset:0;display:flex;align-items:center;justify-content:center;transform:skewX(12deg);
            font-family:"Montserrat",sans-serif;font-style:italic;font-weight:800;font-size:24px;color:var(--ink);letter-spacing:1px}
  .lic b{color:var(--green-deep);font-weight:700}

  .tagline{position:absolute;left:50px;top:300px;font-family:"Anton",sans-serif;transform:skewX(-8deg);line-height:1}
  .tag-build{position:absolute;left:28px;top:0;font-size:96px;color:var(--ink);letter-spacing:-1px}
  .tag-with{position:absolute;left:233px;top:12px;font-size:35px;color:var(--ink);line-height:.95}
  .tag-crew{position:absolute;left:0;top:90px;font-size:102px;color:var(--green-deep);white-space:nowrap}

  .contact-pill{position:absolute;left:731px;top:91px;width:300px;height:52px;border-radius:26px 0 0 26px;
                background:linear-gradient(90deg,#1e1e1e,var(--band-light));display:flex;align-items:center;padding-left:22px;
                font-family:"Montserrat",sans-serif;font-size:33px;color:var(--white);font-weight:300;font-style:italic}
  .contact-pill strong{font-weight:800}
  .contact-rule{position:absolute;left:560px;top:116px;width:160px;height:2px;background:var(--white)}

  .band{position:absolute;right:0;background:linear-gradient(90deg,var(--band-dark),var(--band-light) 55%,var(--band-dark));
        font-family:"Montserrat",sans-serif;font-style:italic;color:var(--white);display:flex;align-items:center;
        white-space:nowrap;padding-right:12px}
  .band-phone{left:567px;top:185px;height:91px;padding-left:42px;font-weight:800;font-size:60px;letter-spacing:-1px}
  .band-web{left:543px;top:317px;height:51px;padding-left:44px;font-weight:700;font-size:17px;letter-spacing:.3px}
  .band-mail{left:560px;top:410px;height:37px;padding-left:40px;font-weight:700;font-size:13px;letter-spacing:.2px}

  .badge{position:absolute;border-radius:50%;border:3px solid var(--green);
         background:radial-gradient(circle at 35% 30%,#fafafa,#c9c9c9 60%,#8d8d8d);box-shadow:0 0 0 3px var(--white)}
  .badge svg{position:absolute;inset:0;margin:auto}
  .badge-phone{left:473px;top:173px;width:114px;height:114px}
  .badge-web{left:496px;top:310px;width:64px;height:64px}
  .badge-mail{left:514px;top:397px;width:62px;height:62px}
</style>
</head>
<body>
<div class="canvas">
  <section class="sign" aria-label="Brookvale Building Company sign">
    <div class="top-panel"></div>

    <svg class="sweep" viewBox="0 0 1020 518" aria-hidden="true">
      <path d="M597 0 Q470 250 567 518 L1020 518 L1020 0 Z" fill="var(--green-shadow)"/>
      <path d="M612 0 Q495 255 585 518 L1020 518 L1020 0 Z" fill="var(--green-mid)"/>
      <path d="M627 0 Q515 260 600 518 L1020 518 L1020 0 Z" fill="var(--green)"/>
      <path d="M634 0 Q524 262 607 518" fill="none" stroke="var(--white)" stroke-width="2"/>
    </svg>

    <div class="brand">
      <span class="brand-mark"></span>
      <div class="brand-name">BROOKVALE</div>
      <div class="brand-sub">BUILDING COMPANY</div>
    </div>

    <div class="lic-rule"></div>
    <div class="lic"><span><b>Lic#</b>4826130</span></div>

    <div class="tagline">
      <div class="tag-build">BUILD</div>
      <div class="tag-with">WITH<br>THE</div>
      <div class="tag-crew">B-CREW!</div>
    </div>

    <div class="contact-rule"></div>
    <div class="contact-pill">CONTACT&nbsp;<strong>US</strong></div>

    <div class="band band-phone">831-555-0172</div>
    <div class="band band-web">BROOKVALEBUILDINGCOMPANY.EXAMPLE</div>
    <div class="band band-mail">BROOKVALEBUILDINGCOMPANY@MAILNEST.EXAMPLE</div>

    <div class="badge badge-phone">
      <svg width="64" height="64" viewBox="0 0 24 24" aria-hidden="true">
        <path d="M6.6 10.8c1.4 2.8 3.8 5.1 6.6 6.6l2.2-2.2c.3-.3.7-.4 1-.2 1.1.4 2.3.6 3.6.6.6 0 1 .4 1 1V20c0 .6-.4 1-1 1C10.6 21 3 13.4 3 4c0-.6.4-1 1-1h3.5c.6 0 1 .4 1 1 0 1.3.2 2.5.6 3.6.1.3 0 .7-.2 1z" fill="var(--ink)"/>
        <path d="M14 2.5a8 8 0 0 1 7.5 7.5M14 5.5a5 5 0 0 1 4.5 4.5M14 8.5a2 2 0 0 1 1.5 1.5" fill="none" stroke="var(--ink)" stroke-width="1.6" stroke-linecap="round"/>
      </svg>
    </div>
    <div class="badge badge-web">
      <svg width="36" height="36" viewBox="0 0 24 24" aria-hidden="true">
        <g fill="none" stroke="var(--ink)" stroke-width="1.2">
          <circle cx="11" cy="11" r="8"/><ellipse cx="11" cy="11" rx="3.5" ry="8"/>
          <path d="M3 11h16M4.5 7h13M4.5 15h13"/>
        </g>
        <path d="M13 12l8 3-3.2 1.2L16.6 20 15 18.6l1.2-3.6z" fill="var(--ink)"/>
      </svg>
    </div>
    <div class="badge badge-mail">
      <svg width="34" height="34" viewBox="0 0 24 24" aria-hidden="true">
        <circle cx="12" cy="12" r="12" fill="var(--ink)"/>
        <rect x="6" y="8" width="12" height="8" fill="none" stroke="var(--white)" stroke-width="1.1"/>
        <path d="M6 8l6 5 6-5M6 16l4.5-4M18 16l-4.5-4" fill="none" stroke="var(--white)" stroke-width="1.1"/>
      </svg>
    </div>
  </section>
</div>
</body>
</html>
```